Website for IT consulting Company

I need a website upgrade, the existing site content is ok, I would also like to add a testimonial page, the site should be something that is easy for us to update content. You use the content from www.kelvanbrook.com as an example. I will also post update logo and artwork. I also need a contact form with some type of validation or captcha.

I added Coded to the Project

Please omit Address maps

Target Market(s)

small business, service oriented companies. We provide IT Consulting, support and mangement

Industry/Entity Type

Information Technology

Coding

Number of Pages Required

1 page

Font styles to use
Serif
Sans Serif

Requirements
Must have
• Contain logo attached, and content from existing web site www.kelvanbrook.com.
• Also need to update content easily, and be movable to different platforms.
• There is a catch phrase
• "Let us worry about your technology…” “ so you don’t have to!”
• Should be included.
Nice to have
• Testimonial page, Project page where we can post new and past projects and pictures
Should not have
• none

```html
<!DOCTYPE html>
<html lang="en">
<head>
<meta charset="utf-8">
<title>Kelvanbrook Technology Group – IT Consulting</title>
<link rel="stylesheet" href="https://fonts.googleapis.com/css2?family=Exo+2:ital,wght@0,700;0,800;1,700;1,800&family=Arimo:wght@400;700&family=Tinos&display=swap">
<style>
:root{
  --black:#000;
  --blue:#1f8fd6;
  --blue-dark:#0f6fb4;
  --blue-light:#35a9ec;
  --ink:#1c1c1c;
  --text:#333;
  --grey-bg:#e6e6e6;
  --grey-arc:#9a9a9a;
  --footer:#2b2726;
  --white:#fff;
}
*{box-sizing:border-box;margin:0;padding:0}
html,body{width:1200px;height:2557px;overflow:hidden}
body{position:relative;background:var(--white);font-family:"Arimo",Arial,sans-serif;color:var(--text)}
.abs{position:absolute}
.display{font-family:"Exo 2",Arial,sans-serif;font-style:italic;font-weight:800}

/* header */
.site-header{left:0;top:0;width:1200px;height:124px;background:var(--black)}
.brand{left:82px;top:28px;display:flex;align-items:center;gap:14px}
.brand-mark{width:62px;height:62px;background:var(--blue);border-radius:8px}
.brand-name{font-family:"Exo 2",sans-serif;font-weight:800;font-size:40px;color:var(--white);letter-spacing:1px}
.brand-tag{left:162px;top:86px;font-size:11px;color:var(--blue-light)}
.follow{font-family:"Exo 2",sans-serif;font-style:italic;font-weight:700;color:var(--white);font-size:18px}
.social{display:flex;gap:8px}
.social span{width:27px;height:27px;background:#d8d8d8;border-radius:3px;display:block}
.header-follow{left:850px;top:16px}
.header-social{left:980px;top:14px}
.contact-chip{display:flex;align-items:center;gap:12px;color:var(--white);font-weight:700}
.chip-icon{width:40px;height:40px;background:var(--blue);border-radius:5px;display:flex;align-items:center;justify-content:center}
.header-phone{left:755px;top:68px;font-size:21px}
.header-support{left:980px;top:68px;font-family:"Exo 2",sans-serif;font-style:italic;font-size:19px}

/* nav */
.main-nav{left:0;top:124px;width:1200px;height:58px;background:linear-gradient(#3aa6e6,#1a82c8)}
.main-nav a{position:absolute;top:17px;font-family:"Exo 2",sans-serif;font-style:italic;font-weight:800;font-size:19px;color:var(--white);text-decoration:none;letter-spacing:.5px}
.main-nav a.current{color:#1d3550}

/* hero */
.hero{left:0;top:182px;width:1200px;height:534px;background:linear-gradient(180deg,#8a9098 0%,#5c646d 35%,#3a3f45 70%,#55504c 100%)}
.hero-mark{left:558px;top:345px;width:85px;height:85px;background:var(--blue);border-radius:12px}
.hero-line1{left:0;width:1200px;top:470px;text-align:center;font-size:34px;color:var(--white)}
.hero-line2{left:0;width:1200px;top:518px;text-align:center;font-size:36px;color:var(--blue)}
.hero-dots{left:570px;top:690px;display:flex;gap:5px}
.hero-dots span{width:10px;height:10px;background:#aaa}
.hero-dots span.on{background:var(--white)}

/* welcome */
.section-title{left:0;width:1200px;text-align:center;font-size:28px;color:var(--ink)}
.section-title em{color:var(--blue);font-style:italic}
.title-rule{left:560px;width:80px;height:3px;background:var(--blue)}
.welcome-text{left:85px;width:1030px;top:822px;text-align:center;font-size:14.5px;line-height:26px;color:#222}
.read-more{left:0;width:1200px;top:917px;text-align:center;font-family:"Exo 2",sans-serif;font-style:italic;font-weight:700;font-size:14px;color:var(--blue-dark);text-decoration:underline}

/* services */
.services{left:0;top:980px;width:1200px;height:575px;background:var(--grey-bg)}
.svc-label{font-family:"Exo 2",sans-serif;font-style:italic;font-weight:800;font-size:16px;color:#222;line-height:17px}

/* panels */
.panel{top:1555px;height:385px}
.panel-support{left:0;width:605px;background:linear-gradient(180deg,#2a9fe4,#1577bd)}
.panel-outsource{left:605px;width:595px;background:linear-gradient(180deg,#d8d8d8,#8a8a8a)}
.panel-notch{left:576px;top:1555px;width:0;height:0;border-left:30px solid transparent;border-right:30px solid transparent;border-top:30px solid var(--grey-bg)}
.panel h3{position:absolute;top:68px;font-size:25px;display:flex;align-items:center;gap:10px}
.panel-support h3{left:85px;color:var(--white)}
.panel-outsource h3{left:30px;color:var(--ink)}
.panel-rule{position:absolute;top:111px;height:1px}
.panel-photo{position:absolute;top:129px;width:205px;height:183px;border:3px solid #eee}
.panel p{position:absolute;top:131px;width:260px;font-size:14.5px;line-height:27px}
.panel-support p{left:310px;color:var(--white)}
.panel-outsource p{left:254px;color:var(--white)}
.btn-more{position:absolute;top:278px;width:150px;height:38px;font-family:"Tinos",serif;font-size:17px;color:var(--white);display:flex;align-items:center;justify-content:center;gap:10px}
.panel-support .btn-more{left:310px;background:linear-gradient(#a9a9a9,#7b7b7b)}
.panel-outsource .btn-more{left:254px;background:var(--blue)}

/* call to action */
.cta-title{left:0;width:1200px;top:1980px;text-align:center;font-size:35px;color:#111}
.cta-sub{left:0;width:1200px;top:2030px;text-align:center;font-size:28px;color:#111}
.cta-btn{left:472px;top:2094px;width:195px;height:48px;border-radius:8px;background:linear-gradient(#8e8e8e,#5a5a5a);display:flex;align-items:center;gap:8px;padding-left:10px;color:var(--white)}
.cta-btn small{display:block;font-family:"Exo 2",sans-serif;font-style:italic;font-weight:700;font-size:15px;line-height:17px}
.cta-btn strong{display:block;font-family:"Exo 2",sans-serif;font-style:italic;font-weight:800;font-size:19px;line-height:20px}
.cta-mark{left:668px;top:2085px;width:60px;height:60px;background:var(--blue);border-radius:8px}

/* footer */
.site-footer{left:0;top:2188px;width:1200px;height:327px;background:linear-gradient(180deg,#2c2828,#3b3633)}
.foot-head{position:absolute;top:2245px;font-family:"Exo 2",sans-serif;font-style:italic;font-weight:800;font-size:18px;color:var(--white)}
.foot-head em{color:var(--blue)}
.foot-head::after{content:"";display:block;width:130px;height:1px;background:#666;margin-top:5px}
.quick-links{left:85px;top:2283px;list-style:none}
.quick-links li{font-size:14px;line-height:25px;color:var(--white);padding-left:18px;position:relative}
.quick-links li::before{content:"";position:absolute;left:0;top:10px;width:4px;height:4px;background:var(--blue)}
.foot-contact{left:286px;top:2283px;font-size:14px;line-height:22px;color:var(--white)}
.foot-row{display:flex;align-items:center;gap:16px;margin-top:16px}
.foot-row svg{flex:none}
.inquiry input,.inquiry textarea{position:absolute;left:598px;width:226px;border:1px solid #ccc;background:var(--white);font-family:"Arimo",sans-serif;font-size:12px;color:#222;padding:4px 6px;resize:none}
.inq-submit{left:602px;top:2435px;width:92px;height:29px;background:var(--blue);border:1px solid #8cc9f0;color:var(--white);font-family:"Exo 2",sans-serif;font-style:italic;font-weight:800;font-size:15px;text-align:center;line-height:27px}
.foot-mark{left:920px;top:2250px;width:180px;height:180px;background:var(--blue);border-radius:22px}

/* bottom bar */
.bottom-bar{left:0;top:2515px;width:1200px;height:42px;background:var(--blue)}
.copyright{left:85px;top:2528px;font-family:"Exo 2",sans-serif;font-style:italic;font-weight:700;font-size:14px;color:var(--white)}
.bottom-follow{left:855px;top:2524px}
.bottom-social{left:980px;top:2523px}
</style>
</head>
<body>

<header class="site-header abs">
</header>
<div class="brand abs"><span class="brand-mark"></span><span class="brand-name">KELVANBROOK</span></div>
<div class="brand-tag abs">Let us worry about your technology... So you don't have to!</div>
<div class="follow header-follow abs">Follow Us On</div>
<div class="social header-social abs"><span></span><span></span><span></span><span></span></div>
<div class="contact-chip header-phone abs">
  <span class="chip-icon"><svg width="22" height="22" viewBox="0 0 24 24"><path fill="#fff" d="M6.6 10.8a15 15 0 0 0 6.6 6.6l2.2-2.2c.3-.3.7-.4 1-.2 1.1.4 2.3.6 3.6.6.6 0 1 .4 1 1V20c0 .6-.4 1-1 1A17 17 0 0 1 3 4c0-.6.4-1 1-1h3.5c.6 0 1 .4 1 1 0 1.3.2 2.5.6 3.6.1.3 0 .7-.2 1z"/></svg></span>
  (555) 014-2290
</div>
<div class="contact-chip header-support abs">
  <span class="chip-icon"><svg width="24" height="24" viewBox="0 0 24 24"><circle cx="10" cy="8" r="4" fill="#fff"/><path fill="#fff" d="M2 21c0-4.4 3.6-7 8-7s8 2.6 8 7z"/></svg></span>
  SUPPORT
</div>

<nav class="main-nav abs">
  <a class="current" style="left:95px">HOME</a>
  <a style="left:217px">ABOUT US</a>
  <a style="left:375px">SERVICES</a>
  <a style="left:534px">PROJECTS</a>
  <a style="left:694px">CLIENTS</a>
  <a style="left:837px">CAREERS</a>
  <a style="left:989px">CONTACT&nbsp; US</a>
</nav>

<section class="hero abs" role="img" aria-label="Aerial photo of a downtown city skyline with office towers under a cloudy sky"></section>
<div class="hero-mark abs"></div>
<div class="hero-line1 display abs">Let Us Worry About Your Technology...</div>
<div class="hero-line2 display abs">So You Don't Have To!</div>
<div class="hero-dots abs"><span></span><span></span><span></span><span class="on"></span></div>

<h1 class="section-title display abs" style="top:757px">WELCOME TO KELVANBROOK <em>TECHNOLOGY GROUP, INC</em></h1>
<div class="title-rule abs" style="top:800px"></div>
<p class="welcome-text abs">Kelvanbrook Technology Group, Inc. was established in 1991. Our mission is helping businesses and individuals realize a Return on Investment by implementing today's advanced technologies. As a small business we understand the importance of technology and personalized attention.&nbsp; Every member of our support team has worked with both large and small companies supporting a multitude of applications, networks and environments.</p>
<div class="read-more abs">READ MORE</div>

<section class="services abs">
  <h2 class="section-title display abs" style="top:42px">OUR <em>SERVICES</em></h2>
  <div class="title-rule abs" style="top:86px"></div>
  <svg class="abs" style="left:0;top:0" width="1200" height="575" viewBox="0 0 1200 575">
    <path d="M330 575 A270 270 0 0 1 870 575 Z" fill="#fff" stroke="var(--grey-arc)" stroke-width="9"/>
    <g stroke="#999" stroke-width="1.5" stroke-dasharray="3 3">
      <line x1="283" y1="483" x2="380" y2="510"/>
      <line x1="341" y1="363" x2="410" y2="425"/>
      <line x1="394" y1="282" x2="460" y2="350"/>
      <line x1="498" y1="219" x2="533" y2="305"/>
      <line x1="617" y1="193" x2="600" y2="285"/>
      <line x1="733" y1="222" x2="667" y2="305"/>
      <line x1="837" y1="282" x2="740" y2="350"/>
      <line x1="916" y1="374" x2="790" y2="425"/>
      <line x1="958" y1="483" x2="820" y2="510"/>
    </g>
    <g fill="#fff" stroke="#999" stroke-width="2">
      <circle cx="380" cy="510" r="7"/><circle cx="410" cy="425" r="7"/><circle cx="460" cy="350" r="7"/>
      <circle cx="533" cy="305" r="7"/><circle cx="600" cy="285" r="7"/><circle cx="667" cy="305" r="7"/>
      <circle cx="740" cy="350" r="7"/><circle cx="790" cy="425" r="7"/><circle cx="820" cy="510" r="7"/>
    </g>
    <g fill="var(--blue)" stroke="#fff" stroke-width="4">
      <circle cx="283" cy="483" r="50"/><circle cx="341" cy="363" r="50"/><circle cx="394" cy="282" r="50"/>
      <circle cx="498" cy="219" r="50"/><circle cx="617" cy="193" r="50"/><circle cx="733" cy="222" r="50"/>
      <circle cx="837" cy="282" r="50"/><circle cx="916" cy="374" r="50"/><circle cx="958" cy="483" r="50"/>
    </g>
    <g fill="none" stroke="#fff" stroke-width="3" stroke-linecap="round">
      <rect x="263" y="468" width="40" height="26" rx="2"/><line x1="258" y1="500" x2="308" y2="500"/>
      <circle cx="336" cy="352" r="8"/><path d="M322 380c0-10 6-15 14-15s14 5 14 15"/><rect x="346" y="360" width="16" height="12"/>
      <line x1="394" y1="274" x2="394" y2="304"/><circle cx="394" cy="272" r="4"/><path d="M383 262a16 16 0 0 0 0 20M405 262a16 16 0 0 1 0 20"/>
      <circle cx="498" cy="219" r="20"/><line x1="492" y1="211" x2="492" y2="227"/><line x1="504" y1="211" x2="504" y2="227"/>
      <rect x="597" y="174" width="40" height="11" rx="2"/><rect x="597" y="188" width="40" height="11" rx="2"/><rect x="597" y="202" width="40" height="11" rx="2"/>
      <rect x="711" y="206" width="32" height="22" rx="2"/><rect x="746" y="212" width="12" height="20" rx="2"/><line x1="721" y1="236" x2="735" y2="236"/>
      <rect x="820" y="270" width="26" height="18" rx="3" transform="rotate(-35 833 279)"/><path d="M843 288l12 14"/>
      <rect x="896" y="380" width="40" height="12" rx="3"/><path d="M906 368a14 14 0 0 1 20 0M901 362a21 21 0 0 1 30 0"/>
      <path d="M958 460l18 7v12c0 12-8 20-18 24-10-4-18-12-18-24v-12z"/><path d="M964 478a7 7 0 1 0 0 10"/>
    </g>
    <rect x="556" y="445" width="60" height="60" rx="8" fill="var(--blue)"/>
    <text x="600" y="545" text-anchor="middle" font-family="Exo 2, sans-serif" font-weight="800" font-size="40" fill="#7a7a7a">KELVANBROOK</text>
  </svg>
  <div class="svc-label abs" style="left:126px;top:473px;text-align:center">DESKTOP<br>SUPPORT</div>
  <div class="svc-label abs" style="left:100px;top:343px;text-align:right">NETWORK<br>ADMINISTRATION</div>
  <div class="svc-label abs" style="left:128px;top:257px">TELECOMMUNICATIONS</div>
  <div class="svc-label abs" style="left:225px;top:182px">AUDIO/VIDEO MULTIMEDIA</div>
  <div class="svc-label abs" style="left:532px;top:125px">DISASTER RECOVERY</div>
  <div class="svc-label abs" style="left:783px;top:172px">WEB DESIGN</div>
  <div class="svc-label abs" style="left:900px;top:257px">NETWORK CABLING</div>
  <div class="svc-label abs" style="left:982px;top:352px">WIRELESS<br>NETWORKS</div>
  <div class="svc-label abs" style="left:1016px;top:463px">ANTIVIRUS<br>SOLUTIONS</div>
</section>

<section class="panel panel-support abs">
  <h3 class="display"><svg width="34" height="34" viewBox="0 0 34 34"><circle cx="17" cy="10" r="7" fill="#fff"/><path d="M4 34c0-9 6-14 13-14s13 5 13 14z" fill="#fff"/></svg>IT SUPPORT SOLUTIONS</h3>
  <div class="panel-rule" style="left:85px;width:490px;background:rgba(255,255,255,.35)"></div>
  <div class="panel-photo" style="left:85px;background:linear-gradient(135deg,#a9c6dc,#3e6f98 55%,#e6eef4)" role="img" aria-label="Photo of two technicians working beside a server rack"></div>
  <p>Lorem ipsum dolor sit amet, consecretk etuer adipiscing elit, sed diam nonumre my nibh euismod tinciduntol ut laoret et re olore magna aliquam erat volutpt. Ut wisi minim consequat.</p>
  <div class="btn-more">Read More <span>&#10230;</span></div>
</section>
<section class="panel panel-outsource abs">
  <h3 class="display"><svg width="34" height="34" viewBox="0 0 34 34"><circle cx="17" cy="9" r="6" fill="#111"/><rect x="6" y="17" width="22" height="3" fill="#111"/><rect x="9" y="20" width="3" height="12" fill="#111"/><rect x="22" y="20" width="3" height="12" fill="#111"/><circle cx="4" cy="14" r="3" fill="#111"/><circle cx="30" cy="14" r="3" fill="#111"/></svg>WHY OUTSOURCE TECHNOLOGIES</h3>
  <div class="panel-rule" style="left:30px;width:520px;background:rgba(0,0,0,.2)"></div>
  <div class="panel-photo" style="left:31px;background:radial-gradient(circle at 55% 40%,#8fd0ff,#1d4f8a 50%,#0c1d3a)" role="img" aria-label="Illustration of a glowing globe with floating screens above an open hand"></div>
  <p>Lorem ipsum dolor sit amet, consecretk etuer adipiscing elit, sed diam nonumre my nibh euismod tinciduntol ut laoret et re olore magna aliquam erat volutpt. Ut wisi minim consequat.</p>
  <div class="btn-more">Read More <span>&#10230;</span></div>
</section>
<div class="panel-notch abs"></div>

<h2 class="cta-title display abs">IT Solutions That Works For Your Business</h2>
<div class="cta-sub display abs">A Full Service Technology Company</div>
<div class="cta-btn abs">
  <svg width="26" height="26" viewBox="0 0 24 24"><path fill="#fff" d="M6.6 10.8a15 15 0 0 0 6.6 6.6l2.2-2.2c.3-.3.7-.4 1-.2 1.1.4 2.3.6 3.6.6.6 0 1 .4 1 1V20c0 .6-.4 1-1 1A17 17 0 0 1 3 4c0-.6.4-1 1-1h3.5c.6 0 1 .4 1 1 0 1.3.2 2.5.6 3.6.1.3 0 .7-.2 1z"/></svg>
  <div><small>Call Us Today</small><strong>(555) 014-2290</strong></div>
</div>
<div class="cta-mark abs"></div>

<footer class="site-footer abs" role="img" aria-label="Dim city skyline at dusk behind the footer"></footer>
<div class="foot-head" style="left:85px">Quick <em>Links</em></div>
<ul class="quick-links abs">
  <li>Home</li><li>About Us</li><li>Services</li><li>Projects</li><li>Clients</li><li>Careers</li><li>Contact Us</li>
</ul>
<div class="foot-head" style="left:286px">Contact <em>Details</em></div>
<div class="foot-contact abs">
  <div>Kelvanbrook Technology Group, Inc.</div>
  <div style="margin-top:14px">418 Marlow Ave.<br>Brenton, Texas 77000</div>
  <div class="foot-row"><svg width="14" height="14" viewBox="0 0 24 24"><path fill="var(--blue)" d="M6.6 10.8a15 15 0 0 0 6.6 6.6l2.2-2.2c.3-.3.7-.4 1-.2 1.1.4 2.3.6 3.6.6.6 0 1 .4 1 1V20c0 .6-.4 1-1 1A17 17 0 0 1 3 4c0-.6.4-1 1-1h3.5c.6 0 1 .4 1 1 0 1.3.2 2.5.6 3.6.1.3 0 .7-.2 1z"/></svg>(555) 014-2290</div>
  <div class="foot-row"><svg width="14" height="14" viewBox="0 0 24 24"><rect x="5" y="2" width="14" height="7" fill="var(--blue)"/><rect x="2" y="9" width="20" height="9" rx="2" fill="var(--blue)"/><rect x="6" y="15" width="12" height="7" fill="var(--blue)"/></svg>(555) 014-2290</div>
  <div class="foot-row"><svg width="14" height="14" viewBox="0 0 24 24"><rect x="2" y="5" width="20" height="14" fill="var(--blue)"/><path d="M2 5l10 8 10-8" fill="none" stroke="#2c2828" stroke-width="2"/></svg>info@kelvanbrook.com</div>
</div>
<div class="foot-head" style="left:598px">Quick <em>Inquiry</em></div>
<form class="inquiry">
  <input type="text" value="Name" style="top:2292px;height:32px">
  <input type="text" value="Email" style="top:2327px;height:33px">
  <textarea style="top:2364px;height:62px">Message</textarea>
  <div class="inq-submit abs">SUBMIT</div>
</form>
<div class="foot-mark abs"></div>

<div class="bottom-bar abs"></div>
<div class="copyright abs">Copyright © 2017 KELVANBROOK Technology Group, Inc. All Rights Reserved.</div>
<div class="follow bottom-follow abs">Follow Us On</div>
<div class="social bottom-social abs"><span></span><span></span><span></span><span></span></div>

</body>
</html>
```